Financial Advisor Resource Firm needs business card design

Need business card design for company in Omaha NE called Meridale Circle. We provide resources to financial advisors....workshop programs, retirement analysis, and insurance planning. I would like to see designs that use grays, greens, black, and white colors. The final design should communicate 'collaboration' and be simple yet attractive to financial planning clients. I will attached our logo and another picture of a puzzle piece coming together. I would like the incorporate the puzzle picture somehow, maybe on the back somehow, with color or just the gray scale....OR, the picture be the front of the card with 'Meridale' definition on it (see upload) and then company logo, employee name, title, address on the back (see ppt uploaded). The following disclosure needs to be included somewhere- Advisory services offered through Stonebrook Assets, LLC.
Updates

I uploaded a svg and ai file of the logo

Target Market(s)

Financial planning clients and financial advisors....so pretty diverse age range of about 40-70.

Industry/Entity Type

Financial Planning

Contact Information for Business Card

Tobias L. Fenwright, MBA
Founder/President
5287 E. Larkin Road
Suite 230
Omaha, NE 68190
Phone- (402) 555-0147
Cell- (402) 555-0183
Fax- (402) 555-0129
email- tobias@meridaleplan.example
web address- www.meridaleplan.example

Colors
1b1b1b
474747
d3d3d3
ffffff
9bcb3c
abd036

Requirements
Must have
• Must include logo provided, must be 2 sided, and must have disclosure...all of these items listed in project description

```html
<!DOCTYPE html>
<html lang="en">
<head>
<meta charset="utf-8">
<title>Meridale Circle – Business Card</title>
<link href="https://fonts.googleapis.com/css2?family=Montserrat:wght@600;700&family=Open+Sans:wght@400;600&display=swap" rel="stylesheet">
<style>
  :root {
    --ink: #1b1b1b;
    --graphite: #474747;
    --mist: #d3d3d3;
    --paper: #ffffff;
    --leaf: #9bcb3c;
    --lime: #abd036;
    --stage: #ecece9;
  }
  * { box-sizing: border-box; margin: 0; padding: 0; }
  html, body { width: 1200px; height: 900px; overflow: hidden; }
  body {
    background: var(--stage);
    display: flex; flex-direction: column; align-items: center; justify-content: center;
    gap: 40px;
    font-family: "Open Sans", Arial, sans-serif;
  }
  .card {
    width: 630px; height: 360px; position: relative; overflow: hidden;
    box-shadow: 0 8px 24px rgba(0,0,0,.18);
  }

  /* Front */
  .card-front { background: var(--ink); color: var(--paper); }
  .front-photo {
    position: absolute; inset: 0;
    background: radial-gradient(ellipse at 60% 40%, #4a4a4a 0%, #2e2e2e 45%, #1b1b1b 100%);
  }
  .front-brand {
    position: absolute; left: 0; right: 0; top: 110px;
    display: flex; align-items: center; justify-content: center; gap: 14px;
  }
  .brand-dot { width: 26px; height: 26px; border-radius: 50%; background: var(--paper); flex: none; }
  .front-brand .brand-name {
    font-family: "Montserrat", Arial, sans-serif; font-weight: 600;
    font-size: 40px; letter-spacing: 3px; color: var(--paper);
  }
  .front-tagline {
    position: absolute; left: 0; right: 0; bottom: 34px; text-align: center;
    font-size: 14px; letter-spacing: 1.6px; text-transform: uppercase; color: var(--paper);
  }

  /* Back */
  .card-back { background: var(--paper); color: var(--graphite); }
  .name-band {
    position: absolute; left: 0; right: 0; top: 20px; height: 66px;
    background: var(--leaf);
    border-top: 3px solid var(--ink); border-bottom: 3px solid var(--ink);
    text-align: center; padding-top: 8px;
  }
  .holder-name {
    font-family: "Montserrat", Arial, sans-serif; font-weight: 700;
    font-size: 22px; color: var(--paper); letter-spacing: .3px;
  }
  .holder-title { font-size: 12px; color: var(--paper); margin-top: 1px; }
  .back-brand {
    position: absolute; left: 30px; top: 174px;
    display: flex; align-items: center; gap: 10px;
  }
  .back-brand .brand-dot { width: 20px; height: 20px; background: var(--leaf); }
  .back-brand .brand-name {
    font-family: "Montserrat", Arial, sans-serif; font-weight: 600;
    font-size: 23px; letter-spacing: 1.5px; color: var(--ink);
  }
  .divider {
    position: absolute; left: 318px; top: 134px; width: 1px; height: 176px; background: var(--mist);
  }
  .contact {
    position: absolute; left: 336px; top: 130px; list-style: none;
    font-size: 14.5px; line-height: 23px; color: var(--graphite);
  }
  .contact li { display: flex; align-items: center; gap: 8px; }
  .contact .address { display: block; line-height: 20px; margin-bottom: 4px; }
  .contact svg { width: 12px; height: 12px; fill: var(--leaf); flex: none; }
  .disclosure {
    position: absolute; left: 0; right: 0; bottom: 12px; text-align: center;
    font-size: 10px; letter-spacing: .3px; color: var(--graphite);
  }
</style>
</head>
<body>

<section class="card card-front">
  <div class="front-photo" role="img" aria-label="Grayscale photograph of hands joining puzzle pieces"></div>
  <div class="front-brand">
    <span class="brand-dot"></span>
    <span class="brand-name">MERIDALE CIRCLE</span>
  </div>
  <p class="front-tagline">To come together and unite in common interest and focus</p>
</section>

<section class="card card-back">
  <header class="name-band">
    <h1 class="holder-name">Tobias L. Fenwright, MBA</h1>
    <p class="holder-title">Founder/President</p>
  </header>

  <div class="back-brand">
    <span class="brand-dot"></span>
    <span class="brand-name">MERIDALE CIRCLE</span>
  </div>

  <div class="divider"></div>

  <ul class="contact">
    <li class="address">5287 E. Larkin Road Suite 230<br>Omaha, NE 68190</li>
    <li><svg viewBox="0 0 24 24" aria-hidden="true"><path d="M6.6 10.8a15 15 0 0 0 6.6 6.6l2.2-2.2c.3-.3.7-.4 1-.2 1.1.4 2.3.6 3.6.6.6 0 1 .4 1 1V20c0 .6-.4 1-1 1A17 17 0 0 1 3 4c0-.6.4-1 1-1h3.5c.6 0 1 .4 1 1 0 1.3.2 2.5.6 3.6.1.3 0 .7-.2 1z"/></svg>(402) 555-0147</li>
    <li><svg viewBox="0 0 24 24" aria-hidden="true"><path d="M7 1h10a2 2 0 0 1 2 2v18a2 2 0 0 1-2 2H7a2 2 0 0 1-2-2V3a2 2 0 0 1 2-2zm0 3v14h10V4zm5 15.5a1 1 0 1 0 0 2 1 1 0 0 0 0-2z"/></svg>(402) 555-0183</li>
    <li><svg viewBox="0 0 24 24" aria-hidden="true"><path d="M6 2h10v6H6zM3 9h18a1 1 0 0 1 1 1v9a1 1 0 0 1-1 1h-2v2H5v-2H3a1 1 0 0 1-1-1v-9a1 1 0 0 1 1-1zm4 8v3h10v-3z"/></svg>(402) 555-0129</li>
    <li><svg viewBox="0 0 24 24" aria-hidden="true"><path d="M2 5h20v2l-10 6L2 7zm0 4.3 10 6 10-6V19H2z"/></svg>tobias@meridaleplan.example</li>
    <li><svg viewBox="0 0 24 24" aria-hidden="true"><path d="M12 2a10 10 0 1 0 0 20 10 10 0 0 0 0-20zm6.9 9h-3a15 15 0 0 0-1.3-5.6A8 8 0 0 1 18.9 11zM12 4c.9 1.2 1.8 3.6 1.9 7h-3.8c.1-3.4 1-5.8 1.9-7zM9.4 5.4A15 15 0 0 0 8.1 11h-3a8 8 0 0 1 4.3-5.6zM5.1 13h3a15 15 0 0 0 1.3 5.6A8 8 0 0 1 5.1 13zM12 20c-.9-1.2-1.8-3.6-1.9-7h3.8c-.1 3.4-1 5.8-1.9 7zm2.6-1.4a15 15 0 0 0 1.3-5.6h3a8 8 0 0 1-4.3 5.6z"/></svg>www.meridaleplan.example</li>
  </ul>

  <p class="disclosure">Advisory services offered through Stonebrook Assets, LLC</p>
</section>

</body>
</html>
```